Business Card for Coastal Tundrabridge Advisory

We need a business card for Coastal Tundrabridge Advisory. The company website address is provided below. The company logo is attached. We provide specialized permafrost services to the mining, transportation, and oil & gas industries. The card should be prepared for:
Matthias Korhonen, PhD.
Coastal Tundrabridge Advisory
PO Box 418259
Quillwater, Alaska 99642
Direct: +1-907-555-0143
Email: mkorhonen@tundrabridgeadvisory.example
Website: www.coastaltundrabridgeadvisory.example

```html
<!DOCTYPE html>
<html lang="en">
<head>
<meta charset="utf-8">
<title>Coastal Tundrabridge Advisory – Business Card</title>
<link href="https://fonts.googleapis.com/css2?family=Lato:wght@400;700&display=swap" rel="stylesheet">
<style>
  :root {
    --page: #d9d9d9;
    --card-dark: #1c1c1c;
    --card-light: #ffffff;
    --ink: #16181d;
    --ink-soft: #2b2d33;
    --wordmark-dark: #3a3a3a;
    --white: #ffffff;
    --rule: #9a9a9a;
  }
  * { box-sizing: border-box; margin: 0; padding: 0; }
  html, body { width: 1200px; height: 901px; overflow: hidden; }
  body {
    background: var(--page);
    font-family: "Lato", sans-serif;
    display: flex;
    flex-direction: column;
    align-items: center;
    justify-content: center;
    gap: 36px;
  }
  .card {
    width: 690px;
    height: 394px;
    border-radius: 26px;
    position: relative;
    box-shadow: 0 6px 18px rgba(0,0,0,0.18);
  }

  /* Back side */
  .card--back {
    background: var(--card-dark);
    color: var(--white);
    display: flex;
    flex-direction: column;
    align-items: center;
    justify-content: center;
    text-align: center;
  }
  .back-wordmark {
    color: var(--wordmark-dark);
    font-weight: 700;
    font-size: 46px;
    line-height: 1.05;
    letter-spacing: 3px;
    text-transform: uppercase;
    margin-bottom: 34px;
  }
  .services-title {
    font-weight: 700;
    font-size: 21px;
    letter-spacing: 0.5px;
    margin-bottom: 8px;
  }
  .services-list {
    font-weight: 400;
    font-size: 22px;
  }

  /* Front side */
  .card--front {
    background: var(--card-light);
    color: var(--ink);
  }
  .front-wordmark {
    position: absolute;
    left: 0; right: 0;
    top: 62px;
    text-align: center;
    font-weight: 700;
    font-size: 46px;
    line-height: 1.05;
    letter-spacing: 3px;
    text-transform: uppercase;
    color: var(--ink);
  }
  .details {
    position: absolute;
    left: 40px;
    right: 40px;
    bottom: 58px;
    display: flex;
    align-items: center;
  }
  .person {
    flex: 0 0 auto;
    text-align: right;
    padding-right: 20px;
  }
  .person-name {
    font-weight: 700;
    font-size: 24px;
    color: var(--ink);
    margin-bottom: 2px;
  }
  .person-line {
    font-size: 14.5px;
    color: var(--ink-soft);
    line-height: 1.4;
  }
  .divider {
    width: 1px;
    align-self: stretch;
    background: linear-gradient(to bottom, transparent, var(--rule) 15%, var(--rule) 85%, transparent);
  }
  .contacts {
    list-style: none;
    padding-left: 16px;
  }
  .contacts li {
    display: flex;
    align-items: center;
    gap: 8px;
    font-size: 14px;
    color: var(--ink-soft);
    line-height: 1.75;
  }
  .contacts svg { width: 15px; height: 15px; flex: 0 0 15px; fill: var(--ink); }
</style>
</head>
<body>

  <section class="card card--back" aria-label="Card back">
    <div class="back-wordmark">Coastal Tundrabridge<br>Advisory</div>
    <p class="services-title">OUR PERMAFROST SERVICES</p>
    <p class="services-list">• Mining • Transportation • Oil &amp; gas industries</p>
  </section>

  <section class="card card--front" aria-label="Card front">
    <div class="front-wordmark">Coastal Tundrabridge<br>Advisory</div>

    <div class="details">
      <div class="person">
        <p class="person-name">Matthias Korhonen, PhD.</p>
        <p class="person-line">Coastal Tundrabridge Advisory</p>
        <p class="person-line">PO Box 418259 Quillwater, Alaska 99642</p>
      </div>
      <div class="divider"></div>
      <ul class="contacts">
        <li>
          <svg viewBox="0 0 24 24" aria-hidden="true"><path d="M6.6 10.8a15.1 15.1 0 0 0 6.6 6.6l2.2-2.2c.3-.3.7-.4 1-.2 1.1.4 2.3.6 3.6.6.6 0 1 .4 1 1V20c0 .6-.4 1-1 1A17 17 0 0 1 3 4c0-.6.4-1 1-1h3.5c.6 0 1 .4 1 1 0 1.3.2 2.5.6 3.6.1.3 0 .7-.2 1z"/></svg>
          +1-907-555-0143
        </li>
        <li>
          <svg viewBox="0 0 24 24" aria-hidden="true"><path d="M2 5h20v14H2z M4 7v.5l8 5 8-5V7l-8 5z" fill-rule="evenodd"/></svg>
          mkorhonen@tundrabridgeadvisory.example
        </li>
        <li>
          <svg viewBox="0 0 24 24" aria-hidden="true"><path d="M12 2a10 10 0 1 0 0 20 10 10 0 0 0 0-20zm0 2c.9 1.2 1.6 2.8 1.9 5h-3.8c.3-2.2 1-3.8 1.9-5zM9.4 4.4C8.8 5.7 8.3 7.2 8.1 9H4.9a8 8 0 0 1 4.5-4.6zm5.2 0A8 8 0 0 1 19.1 9h-3.2c-.2-1.8-.7-3.3-1.3-4.6zM4.3 11h3.7v2H4.3a8 8 0 0 1 0-2zm5.7 0h4v2h-4zm6 0h3.7a8 8 0 0 1 0 2H16zM4.9 15h3.2c.2 1.8.7 3.3 1.3 4.6A8 8 0 0 1 4.9 15zm5.2 0h3.8c-.3 2.2-1 3.8-1.9 5-.9-1.2-1.6-2.8-1.9-5zm5.8 0h3.2a8 8 0 0 1-4.5 4.6c.6-1.3 1.1-2.8 1.3-4.6z"/></svg>
          www.coastaltundrabridgeadvisory.example
        </li>
      </ul>
    </div>
  </section>

</body>
</html>
```